Company web site

Looking for a full responsive(mobile friendly) wordpress implementation

Some material is in the website -- brelvanto.wordpress.com

But looking for a template more consistent with the logo design, and more future looking.

Target Market(s)

Enterprise Clients

Industry/Entity Type

It Company

Font styles to use
Sans Serif

Colors
33a6d7
0255a3
0455a3
cfdeed
85abd2
3176b5

Requirements
Must have
• about, contact information, partner page, success stories, customer testimonials. links to social presence.
• pricing information

```html
<!DOCTYPE html>
<html lang="en">
<head>
<meta charset="utf-8">
<title>Nubivex — Blog</title>
<link rel="stylesheet" href="https://fonts.googleapis.com/css2?family=Exo+2:wght@400;500;600;700&family=Russo+One&family=Open+Sans:wght@400;600;700&family=Lato:wght@400;700&display=swap">
<style>
:root{
  --blue:#33a6d7;
  --blue-deep:#0255a3;
  --blue-soft:#cfdeed;
  --topbar:#5a5a5a;
  --ink:#333;
  --text:#666;
  --muted:#999;
  --line:#e3e3e3;
  --field:#efefef;
  --band:#e2e2e2;
  --footer:#172739;
  --footer-text:#c9d3de;
}
*{box-sizing:border-box;margin:0;padding:0}
html,body{width:1200px;height:2875px;overflow:hidden;background:#fff}
body{position:relative;font-family:"Open Sans",Arial,sans-serif;color:var(--text)}
.abs{position:absolute}

/* top bar */
.topbar{left:0;top:0;width:1200px;height:31px;background:var(--topbar);color:#eee;font-size:12px}
.topbar .phone{left:80px;top:8px;display:flex;align-items:center;gap:8px}
.topbar .social{right:80px;top:0;display:flex}
.topbar .social span{width:31px;height:31px;border-left:1px solid #777;display:flex;align-items:center;justify-content:center}
.topbar .social span:last-child{border-right:1px solid #777}
.topbar .social i{width:9px;height:9px;border-radius:50%;background:#ddd;display:block}

/* header */
.header{left:0;top:31px;width:1200px;height:96px;background:#fff;border-bottom:1px solid var(--line)}
.brand{left:80px;top:30px;display:flex;align-items:center;gap:10px;font-family:"Exo 2",sans-serif;font-weight:700;font-size:28px;color:var(--blue)}
.brand .dot{width:30px;height:30px;border-radius:50%;background:var(--blue)}
.nav{left:0;top:0;height:96px;width:1200px}
.nav a{position:absolute;top:44px;font-family:"Exo 2",sans-serif;font-size:16px;color:#555;text-decoration:none}
.nav .active{top:0;left:857px;width:80px;height:96px;background:var(--blue);color:#fff;display:flex;flex-direction:column;align-items:center;justify-content:center;gap:4px;font-weight:600;font-size:17px}

/* hero */
.hero{left:0;top:127px;width:1200px;height:337px;background:linear-gradient(90deg,#050608 0%,#0a0f16 45%,#16324c 70%,#0d1e30 100%)}
.hero-visual{left:620px;top:0;width:580px;height:337px;background:radial-gradient(ellipse at 60% 45%,#7fb6dc 0%,#2f5f86 30%,rgba(12,24,38,0) 70%)}
.hero h1{left:80px;top:143px;font-family:"Exo 2",sans-serif;font-weight:600;font-size:34px;line-height:42px;color:#fff}
.hero h1 em{font-style:normal;color:var(--blue)}

/* breadcrumb */
.crumbs{left:0;top:464px;width:1200px;height:40px;background:var(--band);font-family:"Lato",sans-serif;font-weight:700;font-size:13px;color:#555;display:flex;align-items:center;padding-left:80px;gap:12px;text-transform:uppercase}
.crumbs .sep{color:#888}
.crumbs .here{color:var(--blue)}

/* page title */
.page-title{left:0;top:566px;width:1200px;text-align:center;font-family:"Russo One",sans-serif;font-size:38px;color:var(--blue);letter-spacing:1px}
.title-rule{left:320px;top:623px;width:560px;height:18px}

/* cards */
.card{background:#fff;border:1px solid var(--line)}
.post{left:80px;top:671px;width:684px;height:926px}
.post .date{position:absolute;left:0;top:0;width:60px;height:85px;border-right:1px solid var(--line);text-align:center;padding-top:10px}
.post .date b{display:block;font-family:"Open Sans",sans-serif;font-size:28px;color:var(--ink);line-height:30px}
.post .date small{display:block;font-size:10px;color:#888;line-height:13px}
.post h2{position:absolute;left:80px;top:18px;font-size:20px;font-weight:600;color:var(--ink)}
.post .author{position:absolute;left:80px;top:52px;font-size:12px;font-weight:700;color:var(--blue)}
.post .photo{position:absolute;left:0;top:96px;width:682px;height:320px;background:linear-gradient(120deg,#0f4a7a 0%,#2f86c4 40%,#8cc7ea 75%,#d7ecf8 100%)}
.post .body{position:absolute;left:20px;top:437px;width:642px;font-size:12.5px;line-height:25.5px;color:#555}
.post .body p+p{margin-top:8px}
.post .meta{position:absolute;left:20px;top:880px;font-size:11.5px;color:#666;display:flex;gap:30px}

.comments{left:80px;top:1626px;width:684px;height:224px}
.card h3{position:absolute;left:16px;top:18px;font-family:"Open Sans",sans-serif;font-weight:400;font-size:22px;color:var(--ink)}
.card .h-rule{position:absolute;left:16px;top:66px;width:84px;height:2px;background:#ccc}
.comment .avatar{position:absolute;left:16px;top:100px;width:72px;height:72px;background:linear-gradient(160deg,#8a8f96,#2d3238)}
.comment .quote{position:absolute;left:112px;top:98px;width:560px;font-size:12px;line-height:20px;color:#666}
.comment .who{position:absolute;left:112px;top:163px;font-size:12px;font-weight:700;color:var(--blue);line-height:22px}

.reply{left:80px;top:1879px;width:684px;height:575px}
.reply .note{position:absolute;left:16px;top:96px;font-size:11.5px;color:#777}
.field{position:absolute}
.field label{display:block;font-size:13px;color:#444;margin-bottom:8px}
.field label b{color:#e0302e;font-weight:400}
.field .box{height:37px;background:var(--field);border:1px solid #e5e5e5}
.captcha{position:absolute;left:350px;top:443px;width:117px;height:41px;background:linear-gradient(90deg,#d9dde2,#aab4bf);font-family:"Exo 2",sans-serif;font-size:22px;color:#1f4b8a;display:flex;align-items:center;justify-content:center;letter-spacing:2px}
.btn{position:absolute;left:16px;top:498px;width:154px;height:41px;border:2px solid #aaa;border-radius:8px;font-size:15px;color:#444;display:flex;align-items:center;justify-content:center}

/* sidebar */
.side{left:792px;width:328px}
.search{top:671px;height:96px}
.search .label{position:absolute;left:20px;top:16px;font-size:15px;color:#333}
.search .box{position:absolute;left:18px;top:45px;width:290px;height:34px;background:#eee;font-size:12px;color:#777;padding:9px 10px}
.cats{top:796px;height:316px}
.cats .label{position:absolute;left:20px;top:14px;font-size:15px;color:#333}
.cats .label-rule{position:absolute;left:20px;top:44px;width:86px;height:2px;background:#ccc}
.cats ul{position:absolute;left:18px;top:55px;width:292px;list-style:none}
.cats li{height:37px;border-bottom:1px solid var(--line);display:flex;align-items:center;justify-content:space-between;padding:0 10px;font-size:12px;color:var(--blue)}
.cats li span{color:#888}
.cats li::before{content:"";width:4px;height:4px;border-radius:50%;background:var(--blue);margin-right:10px}
.cats li .n{margin-left:auto}
.cats li.on{background:#c2e2f3;color:#246d99}
.tabs{top:1137px;height:276px}
.tabs .tabrow{position:absolute;left:18px;top:14px;width:292px;display:flex;justify-content:space-between;font-size:14px;color:#333;padding-right:8px}
.tabs .tabline{position:absolute;left:18px;top:42px;width:80px;height:2px;background:var(--blue)}
.tabs .item{position:absolute;left:18px;width:292px;height:50px}
.tabs .thumb{position:absolute;left:0;top:0;width:48px;height:48px;background:linear-gradient(135deg,#174a78,#5fa9dd)}
.tabs .t{position:absolute;left:58px;top:-2px;font-size:12.5px;color:#333;line-height:18px}
.tabs .d{position:absolute;left:58px;top:36px;font-size:11px;color:#999}

/* footer */
.footer{left:0;top:2527px;width:1200px;height:303px;background:var(--footer);color:var(--footer-text);font-size:13.5px}
.footer h4{position:absolute;top:48px;font-family:"Exo 2",sans-serif;font-weight:500;font-size:19px;color:#fff}
.footer h4 em{font-style:normal;color:var(--blue)}
.footer .hr{position:absolute;top:82px;height:1px;background:#3a4b5e}
.links{position:absolute;left:80px;top:106px;list-style:none;line-height:28.5px}
.links li::before{content:"•";margin-right:10px}
.links li.on{color:var(--blue)}
.contact{position:absolute;left:290px;top:106px;line-height:21px;width:280px}
.contact b{color:#fff}
.contact .row{display:flex;align-items:center;gap:10px;margin-top:8px}
.map{position:absolute;left:586px;top:112px;width:242px;height:153px;background:linear-gradient(135deg,#e6e4df,#cfd4d8)}
.f-brand{position:absolute;left:888px;top:190px;font-family:"Exo 2",sans-serif;font-weight:700;font-size:30px;color:var(--blue);display:flex;align-items:center;gap:10px}
.f-brand .dot{width:30px;height:30px;border-radius:50%;background:var(--blue)}
.f-social{position:absolute;left:932px;top:240px;display:flex;gap:22px}
.f-social i{width:12px;height:12px;border-radius:50%;background:#fff;display:block}
.copy{left:0;top:2830px;width:1200px;height:45px;background:var(--blue);color:#fff;font-size:13.5px;display:flex;align-items:center;justify-content:center}
.copy b{margin:0 4px}
</style>
</head>
<body>

<div class="abs topbar">
  <div class="abs phone">
    <svg width="13" height="13" viewBox="0 0 24 24"><path fill="#eee" d="M6.6 10.8a15 15 0 006.6 6.6l2.2-2.2c.3-.3.7-.4 1-.2 1.1.4 2.3.6 3.6.6.6 0 1 .4 1 1V20c0 .6-.4 1-1 1A17 17 0 013 4c0-.6.4-1 1-1h3.5c.6 0 1 .4 1 1 0 1.3.2 2.5.6 3.6.1.3 0 .7-.2 1z"/></svg>
    <span>Call Us : <b>+123 456 7890</b></span>
  </div>
  <div class="abs social"><span><i></i></span><span><i></i></span><span><i></i></span><span><i></i></span></div>
</div>

<header class="abs header">
  <div class="abs brand"><span class="dot"></span>Nubivex</div>
  <nav class="abs nav">
    <a style="left:561px">Home</a>
    <a style="left:644px">Platform</a>
    <a style="left:750px">Partners</a>
    <a class="active">
      <svg width="22" height="20" viewBox="0 0 24 22"><path fill="#fff" d="M3 2h18a2 2 0 012 2v11a2 2 0 01-2 2H10l-5 4v-4H3a2 2 0 01-2-2V4a2 2 0 012-2z"/><circle cx="8" cy="9.5" r="1.4" fill="#33a6d7"/><circle cx="12" cy="9.5" r="1.4" fill="#33a6d7"/><circle cx="16" cy="9.5" r="1.4" fill="#33a6d7"/></svg>
      Blog
    </a>
    <a style="left:974px">About</a>
    <a style="left:1058px">Contact</a>
  </nav>
</header>

<section class="abs hero">
  <div class="abs hero-visual" role="img" aria-label="Hand holding a tablet with a glowing globe and floating screens of connected devices"></div>
  <h1 class="abs">Bridging <em>Connected Devices</em><br>With <em>Enterprise Solutions</em></h1>
</section>

<div class="abs crumbs"><span>Home</span><span class="sep">»</span><span>Blog</span><span class="sep">»</span><span class="here">Lorem ipsum is not simply random text</span></div>

<h1 class="abs page-title">LOREM IPSUM IS NOT SIMPLY RANDOM TEXT</h1>
<svg class="abs title-rule" viewBox="0 0 560 18"><line x1="0" y1="9" x2="255" y2="9" stroke="#ccc"/><line x1="305" y1="9" x2="560" y2="9" stroke="#ccc"/><path d="M268 13h24a5 5 0 000-10 8 8 0 00-15-1 5 5 0 00-9 6 3 3 0 000 5z" fill="none" stroke="#aaa" stroke-width="1.5"/></svg>

<article class="abs card post">
  <div class="date"><b>03</b><small>JUL</small><small>2017</small></div>
  <h2>Lorem Ipsum is not simply random text</h2>
  <div class="author">&#9679; Admin</div>
  <div class="photo" role="img" aria-label="Businessman touching a floating network of gears"></div>
  <div class="body">
    <p>Lorem ipsum dolor sit amet, consectetur adipiscing elit. Mauris consequat luctus nisl nec malesuada. Cras ultrices sed ante quis varius. Curabitur bibendum eros purus, placerat accumsan diam fringilla vel. Fusce ac purus eget quam accumsan luctus. Pellentesque risus nunc, elementum at ultricies eget, egestas ut erat. Phasellus eget aliquet sapien, a lobortis massa. Praesent nec varius massa. Mauris eleifend felis nulla, at tincidunt risus consequat ut. Etiam sit amet orci ut mi feugiat feugiat eu eget risus. Maecenas volutpat purus ac consequat pulvinar. Cras turpis ex, semper non pretium a, tincidunt nec tortor. Mauris cursus dui efficitur nisi sollicitudin varius. Sed id mauris quis nunc condimentum gravida at ut dolor. Nunc ac pellentesque odio, et luctus nibh. Donec quis dignissim risus, sed iaculis tellus.</p>
    <p>Pellentesque posuere, quam sit amet laoreet rutrum, magna est pretium lectus, sit amet vulputate libero erat ut odio. Nullam maximus nulla nec felis molestie, eu aliquam diam viverra. Aenean tristique sagittis diam, et suscipit nunc eleifend in. Quisque eu gravida leo. Quisque arcu sapien, aliquet et ligula nec, consequat interdum justo. Suspendisse varius, leo et aliquam tempus, sapien arcu condimentum leo, sit amet lobortis urna nunc ac nibh. Aenean et luctus quam. Nam gravida, nunc efficitur pulvinar mollis, risus lorem suscipit tortor, id porttitor est sem eget turpis. Sed cursus commodo ipsum ut iaculis. Praesent justo elit, scelerisque ac dui non, accumsan rutrum est. Curabitur tempor varius arcu in laoreet. Sed mollis varius felis sit amet condimentum. Cras at lorem fermentum, eleifend est nec, maximus elit. Curabitur pulvinar pretium enim in semper.</p>
  </div>
  <div class="meta"><span>&#9633; Comments : 0</span><span>&lt; Share It</span></div>
</article>

<section class="abs card comments comment">
  <h3>Comments</h3><div class="h-rule"></div>
  <div class="avatar" role="img" aria-label="Commenter portrait"></div>
  <p class="quote">&ldquo; Lorem Ipsum is simply dummy text of the printing and typesetting industry. Lorem Ipsum has been the industry's standard dummy text ever since the 1500s, when an unknown printer took a galley of type and scrambled it to make a type specimen book. &rdquo;</p>
  <div class="who">Dr. Halvorsen<br>JUL 03, 2017 &nbsp;| 12:14 am</div>
</section>

<section class="abs card reply">
  <h3>Leave A Reply</h3><div class="h-rule"></div>
  <p class="note">Your email address will not be published. Required fields are marked *</p>
  <div class="field" style="left:16px;top:135px;width:318px"><label>First Name <b>*</b></label><div class="box"></div></div>
  <div class="field" style="left:350px;top:135px;width:318px"><label>Last Name <b>*</b></label><div class="box"></div></div>
  <div class="field" style="left:16px;top:213px;width:318px"><label>Email <b>*</b></label><div class="box"></div></div>
  <div class="field" style="left:350px;top:213px;width:318px"><label>Website</label><div class="box"></div></div>
  <div class="field" style="left:16px;top:291px;width:652px"><label>Comment <b>*</b></label><div class="box" style="height:88px"></div></div>
  <div class="field" style="left:16px;top:421px;width:318px"><label>Captcha code <b>*</b></label><div class="box"></div></div>
  <div class="captcha">4 AUE</div>
  <div class="btn">Post Comment</div>
</section>

<aside class="abs card side search">
  <div class="label">Search</div>
  <div class="box">&#9906; Search Now !</div>
</aside>

<aside class="abs card side cats">
  <div class="label">Categories</div><div class="label-rule"></div>
  <ul>
    <li>Lorem Ipsum<span class="n">(8)</span></li>
    <li>Lorem Ipsum<span class="n">(28)</span></li>
    <li>Lorem Ipsum<span class="n">(4)</span></li>
    <li class="on">Lorem Ipsum<span class="n">(1)</span></li>
    <li>Lorem Ipsum<span class="n">(2)</span></li>
    <li>Lorem Ipsum<span class="n">(1)</span></li>
    <li>Lorem Ipsum<span class="n">(1)</span></li>
  </ul>
</aside>

<aside class="abs card side tabs">
  <div class="tabrow"><span>Recent Posts</span><span>Popular Posts</span><span>Tags</span></div>
  <div class="tabline"></div>
  <div class="item" style="top:62px"><div class="thumb" role="img" aria-label="Post thumbnail"></div><div class="t">Lorem ipsum is not simply random<br>text.</div><div class="d">&#9633; Jul 03, 2017</div></div>
  <div class="item" style="top:134px"><div class="thumb" role="img" aria-label="Post thumbnail"></div><div class="t">Lorem ipsum is not simply random<br>text.</div><div class="d">&#9633; Jul 03, 2017</div></div>
  <div class="item" style="top:206px"><div class="thumb" role="img" aria-label="Post thumbnail"></div><div class="t">Lorem ipsum is not simply random<br>text.</div><div class="d">&#9633; Jul 03, 2017</div></div>
</aside>

<footer class="abs footer">
  <h4 style="left:80px">Quick <em>Links</em></h4><div class="hr" style="left:80px;width:135px"></div>
  <ul class="links"><li class="on">Home</li><li>Platform</li><li>Partners</li><li>Blog</li><li>About</li><li>Contact</li></ul>
  <h4 style="left:290px">Contact <em>Details</em></h4><div class="hr" style="left:290px;width:170px"></div>
  <div class="contact">
    <b>Nubivex</b><br>123, Lorem ipsum dolor sit amet,<br>euismod - 123 456
    <div class="row"><svg width="13" height="13" viewBox="0 0 24 24"><path fill="#33a6d7" d="M6.6 10.8a15 15 0 006.6 6.6l2.2-2.2c.3-.3.7-.4 1-.2 1.1.4 2.3.6 3.6.6.6 0 1 .4 1 1V20c0 .6-.4 1-1 1A17 17 0 013 4c0-.6.4-1 1-1h3.5c.6 0 1 .4 1 1 0 1.3.2 2.5.6 3.6.1.3 0 .7-.2 1z"/></svg>123 456 7890</div>
    <div class="row"><svg width="13" height="13" viewBox="0 0 24 24"><rect x="3" y="8" width="18" height="10" fill="#33a6d7"/><rect x="6" y="3" width="12" height="5" fill="#33a6d7"/></svg>123 456 7890</div>
    <div class="row"><svg width="13" height="11" viewBox="0 0 24 18"><rect x="1" y="1" width="22" height="16" fill="#33a6d7"/><path d="M1 1l11 8 11-8" stroke="#172739" fill="none" stroke-width="2"/></svg>info@nubivex.com</div>
  </div>
  <h4 style="left:586px">Location <em>Map</em></h4><div class="hr" style="left:586px;width:140px"></div>
  <div class="map" role="img" aria-label="Street map with a pin at 418 Larkspur Avenue"></div>
  <div class="f-brand"><span class="dot"></span>Nubivex</div>
  <div class="f-social"><i></i><i></i><i></i><i></i></div>
</footer>

<div class="abs copy">Copyright &copy; 2017 <b>Nubivex</b>. All Right Reserved.</div>

</body>
</html>
```